Classic and neutral book cover design

We are looking for a classic and neutral book cover design to be used as the template for a series of books to be published. We are hence looking for a template that will allow us to easily change the title name for all books in this series.
The use of very few colours (black and white is welcome) and few design elements is a big bonus. As a source of inspiration we would like to ask you to view the very simple and
If you think you have a cool idea that can add a twist to the formal classic look don't hesitate. Go for it !
Work will be done for a 30 year old Sweden based cultural non-profit called VĂ©ru (www.verufoundation.example). We work with the publishing and supporting of post-modern art and literature addressing contemporary topics but are also involved in assisting projects of cultural preservation.
Target Market(s)
The audience is expected to have some form of interest in culture but could range from hobbyist readers to tenure track scholars
Industry/Entity Type
Non-Profit
Requirements
Must have
- General:
- Classic and neutral feel
- Preferably very simple and few shapes
- usage of few colours (black and white is welcome)
Information to be displayed on the cover is:
- Author
- Title
- type of work e.g. play/novel (optional)
- publishing house (in this case "Veru Publishing")
Nice to have
- ideas to prevent it from become boring are of course welcome
Should not have
- - too many colours

```html
<!DOCTYPE html>
<html lang="en">
<head>
<meta charset="utf-8">
<title>Book Cover – Veru Publishing</title>
<link rel="stylesheet" href="https://fonts.googleapis.com/css2?family=EB+Garamond:ital,wght@0,400;1,400&display=swap">
<style>
  :root {
    --paper: #ffffff;
    --ink: #111111;
  }
  html, body {
    margin: 0;
    padding: 0;
    width: 952px;
    height: 1200px;
    overflow: hidden;
    background: var(--paper);
  }
  .cover {
    position: relative;
    width: 952px;
    height: 1200px;
    background: var(--paper);
    color: var(--ink);
    font-family: "EB Garamond", Georgia, serif;
  }
  .frame-outer {
    position: absolute;
    left: 46px;
    top: 46px;
    width: 860px;
    height: 1108px;
    border: 1.5px solid var(--ink);
    box-sizing: border-box;
  }
  .frame-inner {
    position: absolute;
    left: 54px;
    top: 54px;
    width: 844px;
    height: 1093px;
    border: 1px solid var(--ink);
    box-sizing: border-box;
  }
  .line {
    position: absolute;
    left: 0;
    width: 100%;
    margin: 0;
    text-align: center;
    line-height: 1;
    font-weight: 400;
  }
  .publisher {
    top: 181px;
    font-style: italic;
    font-size: 18px;
    letter-spacing: 0.22em;
    text-transform: uppercase;
  }
  .title {
    top: 410px;
    font-style: italic;
    font-size: 100px;
    letter-spacing: 0.2em;
    text-transform: uppercase;
    padding-left: 0.2em;
    box-sizing: border-box;
  }
  .work-type {
    top: 786px;
    font-style: italic;
    font-size: 28px;
  }
  .byline {
    top: 840px;
    font-style: italic;
    font-size: 18px;
  }
  .author {
    top: 874px;
    font-size: 31px;
    letter-spacing: 0.14em;
  }
</style>
</head>
<body>
  <main class="cover">
    <div class="frame-outer"></div>
    <div class="frame-inner"></div>
    <p class="line publisher">Veru Publishing</p>
    <h1 class="line title">Nice Title</h1>
    <p class="line work-type">Novel</p>
    <p class="line byline">by</p>
    <p class="line author">Author Authorson</p>
  </main>
</body>
</html>
```